Oriel Photography Business Card

I need a business card designed for a photography business based in Perth, Western Australia called Oriel Photography.

We specialise in wedding, event photography and portrait photography.

The business card must borrow the style of the attached logo.

The hex codes for the colours in the logo are:
#ED1D85 - Pink
#89C23E - Green
#37282F - Black

The name on the card will be:
Name: Tobrian
Phone: 0417395268
Website: www.orielphotography.example.com.au
Facebook: orielphotography

I am open and happy to accept creative concepts.

I’d like some space at the back for writing notes and appointment details.

```html
<!DOCTYPE html>
<html lang="en">
<head>
<meta charset="utf-8">
<title>Oriel Photography Business Card</title>
<link href="https://fonts.googleapis.com/css2?family=Cinzel:wght@400&family=Source+Sans+3:ital,wght@0,400;0,600;0,700;1,400&display=swap" rel="stylesheet">
<style>
  :root {
    --pink: #ED1D85;
    --green: #89C23E;
    --ink: #37282F;
    --grey: #55575a;
    --rule: #9a9a9a;
    --paper: #ffffff;
    --backdrop: #ecebe8;
  }
  * { box-sizing: border-box; margin: 0; padding: 0; }
  html, body { width: 1200px; height: 720px; overflow: hidden; }
  body {
    background: var(--backdrop);
    font-family: "Source Sans 3", Arial, sans-serif;
    color: var(--ink);
    position: relative;
  }
  .card {
    position: absolute;
    top: 205px;
    width: 540px;
    height: 310px;
    background: var(--paper);
    box-shadow: 0 6px 18px rgba(0,0,0,.15);
    overflow: hidden;
  }
  .card--front { left: 40px; }
  .card--back { left: 620px; }

  /* front */
  .front-waves { position: absolute; inset: 0; }
  .brand {
    position: absolute;
    display: flex;
    align-items: center;
    gap: 10px;
  }
  .brand__dot {
    width: 46px; height: 46px;
    border-radius: 50%;
    background: var(--pink);
    flex: none;
  }
  .brand__name {
    font-family: "Source Sans 3", Arial, sans-serif;
    font-weight: 400;
    color: var(--ink);
    text-transform: uppercase;
    letter-spacing: .42em;
    font-size: 15px;
    white-space: nowrap;
  }
  .card--front .brand { left: 60px; top: 60px; }
  .holder {
    position: absolute;
    left: 50px; top: 170px;
    font-weight: 700;
    font-size: 19px;
    letter-spacing: .03em;
    color: var(--pink);
    text-transform: uppercase;
  }
  .contacts {
    position: absolute;
    right: 18px; top: 118px;
    list-style: none;
    display: flex;
    flex-direction: column;
    align-items: flex-end;
    gap: 10px;
    font-size: 13.5px;
    color: var(--ink);
  }
  .contacts li { display: flex; align-items: center; gap: 6px; }
  .contacts svg { width: 13px; height: 13px; flex: none; }

  /* back */
  .card--back .brand { right: 22px; top: 22px; gap: 8px; }
  .card--back .brand__dot { width: 34px; height: 34px; }
  .card--back .brand__name { font-size: 10px; letter-spacing: .3em; }
  .appt-title {
    position: absolute;
    left: 30px; top: 84px;
    font-family: "Cinzel", Georgia, serif;
    font-size: 17px;
    color: var(--pink);
    letter-spacing: .03em;
  }
  .appt-title::after {
    content: "";
    position: absolute;
    left: 216px; bottom: 4px;
    width: 270px;
    border-bottom: 1px dotted var(--rule);
  }
  .row {
    position: absolute;
    left: 30px;
    display: flex;
    align-items: flex-end;
    gap: 6px;
    font-size: 14px;
    color: var(--grey);
  }
  .row--name { top: 124px; }
  .row--date { top: 156px; }
  .row--next { top: 190px; }
  .row--days { top: 226px; gap: 8px; font-weight: 700; font-size: 14px; }
  .line {
    display: inline-block;
    border-bottom: 1px dotted var(--rule);
    height: 14px;
  }
  .box {
    display: inline-block;
    border: 1px solid var(--grey);
    border-radius: 3px;
    width: 120px;
    height: 22px;
  }
  .tick {
    display: inline-block;
    width: 26px; height: 20px;
    border: 1px solid var(--grey);
    border-radius: 3px;
    margin-right: 6px;
  }
  .notice {
    position: absolute;
    left: 30px; top: 266px;
    font-style: italic;
    font-size: 14px;
    color: var(--grey);
  }
</style>
</head>
<body>

  <section class="card card--front" aria-label="Business card front">
    <svg class="front-waves" viewBox="0 0 540 310" preserveAspectRatio="none" aria-hidden="true">
      <path d="M175,310 C320,290 390,120 540,72 L540,310 Z" fill="var(--green)"/>
      <path d="M95,296 C270,286 380,110 540,50 L540,66 C390,120 300,286 150,306 Z" fill="var(--pink)"/>
      <path d="M120,306 C290,290 385,115 540,60 L540,64 C390,122 300,292 140,308 Z" fill="var(--paper)"/>
      <path d="M0,300 C60,296 90,300 120,310 L0,310 Z" fill="var(--pink)"/>
    </svg>

    <div class="brand">
      <span class="brand__dot"></span>
      <span class="brand__name">Oriel Photography</span>
    </div>

    <p class="holder">Tobrian</p>

    <ul class="contacts">
      <li>
        <svg viewBox="0 0 16 16" aria-hidden="true"><circle cx="8" cy="8" r="7.2" fill="none" stroke="var(--ink)" stroke-width="1.4"/><path d="M5.2 4.4l1.4-.3.8 2-1 .8c.5 1.1 1.3 1.9 2.4 2.4l.8-1 2 .8-.3 1.4c-3.3.3-6.4-2.8-6.1-6.1z" fill="var(--ink)"/></svg>
        0417395268
      </li>
      <li>
        <svg viewBox="0 0 16 16" aria-hidden="true"><rect x="1" y="1" width="14" height="14" rx="2" fill="var(--ink)"/></svg>
        orielphotography
      </li>
      <li>
        <svg viewBox="0 0 16 16" aria-hidden="true"><circle cx="8" cy="8" r="7" fill="var(--ink)"/></svg>
        www.orielphotography.example.com.au
      </li>
    </ul>
  </section>

  <section class="card card--back" aria-label="Business card back, appointment details">
    <div class="brand">
      <span class="brand__dot"></span>
      <span class="brand__name">Oriel Photography</span>
    </div>

    <h2 class="appt-title">Your Appointment</h2>

    <div class="row row--name">
      Name : <span class="line" style="width:150px"></span>
      Time : <span class="line" style="width:90px"></span> am / pm
    </div>
    <div class="row row--date">
      Date : <span class="line" style="width:150px"></span>
      <span class="box"></span><span class="box"></span>
    </div>
    <div class="row row--next">
      Next Appointment <span class="box"></span>
    </div>
    <div class="row row--days">
      <span>MON</span><span class="tick"></span>
      <span>TUE</span><span class="tick"></span>
      <span>WED</span><span class="tick"></span>
      <span>THU</span><span class="tick"></span>
      <span>FRI</span><span class="tick"></span>
      <span>SAT</span><span class="tick"></span>
    </div>
    <p class="notice">We appreciate a 24 hr. notice for cancellations</p>
  </section>

</body>
</html>
```